Redesign kavrin.ch agency website for unique design with speed and conversion

We want to redesign our website kavrin.ch. Our omnichannel marketing agency builds webshops and integrates them into existing systems like ERP/CRM and supports with online marketing campaigns like quorvex ads and social media. The target of the redesign is to get a great look and feel for customers to see directly what we do, (please design something for our three focus areas eCommerce, Online marketing and Integration)
and to improve the pages speed drastically for SEO. Please see our attachment.
B2B
eCommerce Agency
Coded - Design and coding required
5+ page

```html
<!DOCTYPE html>
<html lang="en">
<head>
<meta charset="utf-8">
<title>Kavrin – Omnichannel Marketing Agency</title>
<link rel="stylesheet" href="https://fonts.googleapis.com/css2?family=Inter:wght@400;500;600;700&display=swap">
<style>
:root{
  --green:#3cd24a;
  --ink:#111318;
  --text:#222;
  --night:#0b0d10;
  --field:#fff;
  --page:#fff;
}
*{box-sizing:border-box;margin:0;padding:0}
html,body{width:1200px;height:4521px;overflow:hidden}
body{position:relative;background:var(--page);font-family:"Inter",Arial,sans-serif;color:var(--text)}
.abs{position:absolute}
a{color:inherit;text-decoration:none}
.btn{position:absolute;display:flex;align-items:center;justify-content:center;background:var(--green);color:#111;font-weight:600;border-radius:4px;font-size:18px}
.brand{font-family:"Inter",Arial,sans-serif;font-weight:700;color:var(--green);letter-spacing:2px}

/* header */
.site-header{top:0;left:0;width:1200px;height:110px;background:#fff}
.header-logo{left:100px;top:38px;font-size:40px}
.topbar-item{top:20px;font-size:16px;color:#222;display:flex;align-items:center;gap:12px}
.nav-bar{left:316px;top:60px;width:884px;height:50px;background:#000;clip-path:polygon(45px 0,100% 0,100% 100%,0 100%)}
.nav-links{left:409px;top:74px;display:flex;gap:12px;font-size:15px;color:#fff;white-space:nowrap}
.nav-links .active{color:var(--green);border-bottom:2px solid var(--green);padding-bottom:2px}
.social{top:68px;width:34px;height:34px;border:2px solid #fff;border-radius:50%}

/* hero */
.hero{top:110px;left:0;width:1200px;height:578px;background:linear-gradient(110deg,#16283a 0%,#13283a 45%,#1f4457 75%,#0f2130 100%)}
.hero-title{left:100px;top:218px;color:#fff;font-weight:500;line-height:1.15}
.hero-title .small{font-size:50px;font-weight:400;display:block}
.hero-title .big{font-size:52px;display:block}
.hero-text{left:100px;top:404px;width:530px;color:#fff;font-size:14.5px;line-height:25px}
.hero-arrow{top:370px}

/* who */
.who-title{left:100px;top:768px;font-size:34px;font-weight:500;color:var(--ink)}
.rule{height:3px;background:var(--green)}
.who-lead{left:100px;top:838px;width:500px;font-size:24px;line-height:35px;color:var(--ink)}
.who-lead em{font-style:normal;color:var(--green)}
.who-copy{left:638px;top:762px;width:462px;font-size:15px;line-height:30px;color:#222}
.photo{position:absolute}

/* values */
.values-band{left:0;top:1982px;width:1200px;height:242px;background:linear-gradient(90deg,#dfe6ec 0%,#5f7e96 20%,#173550 50%,#0f2a44 80%,#1b3a52 100%)}
.values-title{left:33px;top:1722px;font-size:34px;font-weight:500;color:var(--ink)}
.values-copy{left:33px;top:1786px;width:375px;font-size:14px;line-height:30px;color:#222}
.card{position:absolute;top:1728px;height:351px;background:#fff;border-radius:22px;box-shadow:0 4px 18px rgba(0,0,0,.12);text-align:center}
.card-icon{margin:22px auto 0;display:block}
.card h3{font-size:21px;font-weight:600;color:var(--ink);margin-top:6px;white-space:nowrap}
.card p{font-size:14.5px;line-height:25.5px;color:#444;margin:6px auto 0;width:190px}
.card .outline-btn{display:flex;align-items:center;justify-content:center;width:149px;height:48px;margin:18px auto 0;border:2px solid #222;border-radius:8px;font-size:18px;font-weight:600;color:#111}
.card-accent{left:653px;top:1712px;width:246px;height:370px;border:2px solid var(--green);border-bottom:none;border-right:none;border-radius:24px 0 0 0}

/* focus */
.focus-bg{left:0;top:2561px;width:1200px;height:751px;background:var(--night)}
.focus-video{left:96px;top:2312px;width:1009px;height:479px;background:linear-gradient(135deg,#cfd2d4 0%,#8c8f92 40%,#3c3f44 70%,#6f7276 100%);border:2px solid #fff}
.focus-title{left:0;top:2832px;width:1200px;text-align:center;color:#fff;font-size:35px;font-weight:500}
.focus-item{position:absolute;top:2956px;height:254px;border-left:3px solid var(--green);padding-left:22px;color:#fff;width:330px}
.focus-item h3{font-size:26px;font-weight:500;margin-top:14px}
.focus-item p{font-size:14.5px;line-height:26px;margin-top:8px;width:250px}

/* contact */
.contact-title{left:0;top:3360px;width:1200px;text-align:center;font-size:35px;font-weight:500;color:var(--ink)}
.contact-item{position:absolute;top:3452px;width:300px;text-align:center;font-size:15px;color:#222;line-height:26px}
.contact-item .ic{width:58px;height:58px;border:3px solid var(--green);border-radius:50%;margin:0 auto 12px;display:flex;align-items:center;justify-content:center}
.contact-item strong{font-weight:500;display:block;text-transform:uppercase}
.field{position:absolute;background:var(--field);box-shadow:0 2px 14px rgba(0,0,0,.1);font-size:14.5px;color:#333;padding:18px 30px;display:flex;align-items:center}
.field.area{align-items:flex-start;padding-top:20px}

/* footer */
.site-footer{left:0;top:4138px;width:1200px;height:383px;background:var(--night);color:#fff}
.footer-logo{left:100px;top:4200px;font-size:46px}
.foot-social{top:4286px;width:22px;height:22px;border-radius:50%;background:#fff}
.foot-col{position:absolute;top:4208px;font-size:15px;color:#fff}
.foot-col h4{font-size:20px;font-weight:500;margin-bottom:12px}
.foot-col li{list-style:none;line-height:30px;display:flex;align-items:center;gap:10px}
.foot-col li svg{flex:none}
.foot-line{left:100px;top:4450px;width:1002px;height:1px;background:#444}
.copyright{left:0;top:4472px;width:1200px;text-align:center;font-size:15px;color:#fff}
</style>
</head>
<body>

<!-- Header -->
<header class="abs site-header">
  <div class="abs brand header-logo">KAVRIN</div>
  <div class="abs topbar-item" style="left:480px">
    <svg width="18" height="18" viewBox="0 0 24 24"><path d="M6.6 10.8a15 15 0 0 0 6.6 6.6l2.2-2.2c.3-.3.7-.4 1-.2 1.1.4 2.3.6 3.6.6.6 0 1 .4 1 1V20c0 .6-.4 1-1 1A17 17 0 0 1 3 4c0-.6.4-1 1-1h3.5c.6 0 1 .4 1 1 0 1.3.2 2.5.6 3.6.1.3 0 .7-.2 1z" fill="var(--green)"/></svg>
    +41 44 318 27 60
  </div>
  <div class="abs topbar-item" style="left:727px">
    <svg width="24" height="18" viewBox="0 0 24 18"><rect x="1.5" y="1.5" width="21" height="15" rx="2" fill="none" stroke="var(--green)" stroke-width="2"/><path d="M2 3l10 7 10-7" fill="none" stroke="var(--green)" stroke-width="2"/></svg>
    Mail: info@kavrin.ch
  </div>
  <a class="btn" style="left:954px;top:7px;width:148px;height:46px">Contact Us</a>
  <div class="abs nav-bar"></div>
  <nav class="abs nav-links">
    <a class="active">Home</a><a>• eCommerce</a><a>• Online Marketing</a><a>• Integration</a><a>• Company ▾</a>
  </nav>
  <span class="abs social" style="left:967px"></span>
  <span class="abs social" style="left:1016px"></span>
  <span class="abs social" style="left:1066px"></span>
</header>

<!-- Hero -->
<section class="abs hero" role="img" aria-label="Hand holding a tablet with glowing marketing and network icons on a dark blue background"></section>
<h1 class="abs hero-title"><span class="small">Welcome To</span><span class="big">Omnichannel Marketing<br>Agency</span></h1>
<p class="abs hero-text">Our omnichannel marketing agency builds webshops and integrates them into existing systems like ERP/CRM and supports online marketing campaigns like quorvex ads and social media.</p>
<a class="btn" style="left:98px;top:496px;width:148px;height:50px">Get Started</a>
<svg class="abs hero-arrow" style="left:42px" width="26" height="50" viewBox="0 0 26 50"><path d="M24 2L3 25l21 23" fill="none" stroke="#c9d3da" stroke-width="3"/></svg>
<svg class="abs hero-arrow" style="left:1140px" width="26" height="50" viewBox="0 0 26 50"><path d="M2 2l21 23L2 48" fill="none" stroke="#fff" stroke-width="3"/></svg>

<!-- Who is Kavrin -->
<h2 class="abs who-title">WHO IS KAVRIN?</h2>
<div class="abs rule" style="left:100px;top:818px;width:170px"></div>
<p class="abs who-lead">Kavrin.ch to increas visibility and generate <em>customer inquiries</em> Increase conversions and acquire new <em>B2B customers.</em></p>
<div class="abs who-copy">
  <p>Our goal is to give you added value with strategic online marketing a technological competitive advantage that makes the difference. We build on automated processes for construction and operation<br>your online shop. In this way, we shorten project times, bring web shops online faster and simplify operations.</p>
  <p style="margin-top:30px">we offer you comprehensive advice and coaching for your new shop, for start-ups and restarts. Last but not least, we support Use our skills to find the right online marketing strategy for your business.</p>
</div>
<a class="btn" style="left:638px;top:1110px;width:148px;height:48px">Read More</a>
<div class="photo" style="left:100px;top:993px;width:477px;height:509px;background:radial-gradient(circle at 60% 45%,#e9b56a 0%,#3b5c8f 30%,#0d1f45 70%);box-shadow:0 4px 16px rgba(0,0,0,.2)" role="img" aria-label="Glowing network of connected people icons"></div>
<div class="photo" style="left:316px;top:1191px;width:786px;height:388px;background:linear-gradient(90deg,#50565c 0%,#8d9399 45%,#c3c7ca 70%,#6e7379 100%);border:3px solid #fff;box-shadow:0 6px 20px rgba(0,0,0,.25)" role="img" aria-label="Team meeting in a conference room with a presenter at a screen"></div>
<div class="abs brand" style="left:905px;top:1230px;font-size:30px">KAVRIN</div>

<!-- Company values -->
<div class="abs values-band" role="img" aria-label="Hand holding a tablet with floating icons"></div>
<h2 class="abs values-title">COMPANY VALUES</h2>
<p class="abs values-copy">Do you want to sell your products or services online? But as an SME, don’t you have a marketing department with e-commerce know-how? will face a series of questions essential to the success of your web business crucial are:</p>
<a class="btn" style="left:33px;top:1952px;width:148px;height:48px">Read More</a>

<div class="abs card-accent"></div>
<article class="card" style="left:409px;width:231px">
  <svg class="card-icon" width="60" height="60" viewBox="0 0 60 60" fill="none" stroke="#333" stroke-width="2.5"><path d="M12 28a18 18 0 0 1 30-13M48 32a18 18 0 0 1-30 13"/><path d="M42 8v8h-8M18 52v-8h8"/><circle cx="30" cy="30" r="6" stroke="var(--green)"/></svg>
  <h3>Sustainability</h3>
  <p>It is a long established fact that a reader will be distracted by the readable content of a page when looking at its layout.</p>
  <a class="outline-btn">Read More</a>
</article>
<article class="card" style="left:663px;width:246px">
  <svg class="card-icon" width="64" height="60" viewBox="0 0 64 60" fill="none" stroke-width="2"><path d="M14 4l2 4 4 .5-3 3 .8 4-3.8-2-3.8 2 .8-4-3-3 4-.5zM32 1l2 4 4 .5-3 3 .8 4-3.8-2-3.8 2 .8-4-3-3 4-.5zM50 4l2 4 4 .5-3 3 .8 4-3.8-2-3.8 2 .8-4-3-3 4-.5z" stroke="#333"/><circle cx="32" cy="40" r="16" stroke="var(--green)" stroke-width="3"/><path d="M25 42h4v8h-4zM29 42l4-8c2 0 3 1 2 4h5c1 0 2 1 1.5 2l-2 7c-.3 1-1 1.5-2 1.5H29" stroke="var(--green)"/></svg>
  <h3>Quality</h3>
  <p>It is a long established fact that a reader will be distracted by the readable content of a page when looking at its layout.</p>
  <a class="outline-btn">Read More</a>
</article>
<article class="card" style="left:940px;width:239px">
  <svg class="card-icon" width="66" height="66" viewBox="0 0 66 66" fill="none" stroke-width="2.5"><rect x="20" y="4" width="40" height="58" rx="4" stroke="#333"/><path d="M40 18v26M40 12v2" stroke="#333"/><path d="M6 46l8 8 10-4-6-12c-1-2-4-1-3 1l3 6-6-8c-1-2-4-1-3 1z" stroke="var(--green)"/></svg>
  <h3>Customer orientation</h3>
  <p>It is a long established fact that a reader will be distracted by the readable content of a page when looking at its layout.</p>
  <a class="outline-btn">Read More</a>
</article>

<!-- Our focus -->
<div class="abs focus-bg" role="img" aria-label="Faint dark photo of a team gathered in an office"></div>
<div class="abs focus-video" role="img" aria-label="Business team gathered around a table reviewing documents"></div>
<svg class="abs" style="left:568px;top:2517px" width="64" height="64" viewBox="0 0 64 64"><circle cx="32" cy="32" r="29" fill="rgba(255,255,255,.15)" stroke="#fff" stroke-width="2.5"/><path d="M26 20l18 12-18 12z" fill="#fff"/></svg>
<h2 class="abs focus-title">Our Focus</h2>
<div class="abs rule" style="left:566px;top:2890px;width:68px"></div>

<div class="focus-item" style="left:100px">
  <svg width="92" height="92" viewBox="0 0 92 92" fill="none" stroke="#fff" stroke-width="2.5"><path d="M6 22h62l-4 14H10zM10 36v50h56V36"/><rect x="18" y="46" width="26" height="20"/><rect x="50" y="50" width="10" height="36"/><circle cx="70" cy="20" r="16" fill="var(--night)"/><path d="M54 20h32M70 4c6 8 6 24 0 32M70 4c-6 8-6 24 0 32"/></svg>
  <h3>eCommerce</h3>
  <p>It is a long established fact that a reader will be distracted by the readable content of a page when looking at its layout.</p>
</div>
<div class="focus-item" style="left:465px">
  <svg width="92" height="92" viewBox="0 0 92 92" fill="none" stroke="#fff" stroke-width="2.5"><rect x="22" y="20" width="30" height="60" rx="5"/><path d="M32 26h10"/><rect x="52" y="6" width="30" height="22" rx="3"/><path d="M58 22v-6M64 22v-10M70 22v-4"/><rect x="6" y="8" width="24" height="16" rx="3"/><path d="M36 46l10 10-6 4 8 12"/></svg>
  <h3>Online marketing</h3>
  <p>It is a long established fact that a reader will be distracted by the readable content of a page when looking at its layout.</p>
</div>
<div class="focus-item" style="left:844px">
  <svg width="92" height="92" viewBox="0 0 92 92" fill="none" stroke="#fff" stroke-width="2.5"><path d="M40 10l5 0 2 8 7 3 7-5 4 4-5 7 3 7 8 2v6l-8 2-3 7 5 7-4 4-7-5-7 3-2 8h-6l-2-8-7-3-7 5-4-4 5-7-3-7-8-2v-6l8-2 3-7-5-7 4-4 7 5 7-3z"/><circle cx="42" cy="44" r="12"/><path d="M56 24h20M60 44h24M56 64h20"/><circle cx="78" cy="24" r="3"/><circle cx="86" cy="44" r="3"/><circle cx="78" cy="64" r="3"/></svg>
  <h3>Integration</h3>
  <p>It is a long established fact that a reader will be distracted by the readable content of a page when looking at its layout.</p>
</div>

<!-- Contact -->
<h2 class="abs contact-title">Contact Us</h2>
<div class="contact-item" style="left:17px">
  <div class="ic"><svg width="26" height="26" viewBox="0 0 24 24"><path d="M6.6 10.8a15 15 0 0 0 6.6 6.6l2.2-2.2c.3-.3.7-.4 1-.2 1.1.4 2.3.6 3.6.6.6 0 1 .4 1 1V20c0 .6-.4 1-1 1A17 17 0 0 1 3 4c0-.6.4-1 1-1h3.5c.6 0 1 .4 1 1 0 1.3.2 2.5.6 3.6.1.3 0 .7-.2 1z" fill="var(--green)"/></svg></div>
  <strong>Phone</strong>+41 44 318 27 60
</div>
<div class="contact-item" style="left:411px">
  <div class="ic"><svg width="24" height="30" viewBox="0 0 24 30"><path d="M12 2a9 9 0 0 0-9 9c0 7 9 17 9 17s9-10 9-17a9 9 0 0 0-9-9z" fill="none" stroke="var(--green)" stroke-width="2.5"/><circle cx="12" cy="11" r="3.5" fill="var(--green)"/></svg></div>
  <strong>Address</strong>Lindenweg 12,<br>8003 Zurich, Switzerland
</div>
<div class="contact-item" style="left:804px">
  <div class="ic" style="background:var(--green)"><svg width="26" height="20" viewBox="0 0 24 18"><rect x="1" y="1" width="22" height="16" rx="2" fill="#fff"/><path d="M2 3l10 7 10-7" fill="none" stroke="var(--green)" stroke-width="2"/></svg></div>
  <strong>Email</strong>info@kavrin.ch
</div>

<form>
  <div class="field" style="left:130px;top:3662px;width:454px;height:57px">Name First</div>
  <div class="field" style="left:614px;top:3662px;width:454px;height:57px">Last First</div>
  <div class="field" style="left:130px;top:3747px;width:945px;height:54px">Email Address</div>
  <div class="field" style="left:130px;top:3827px;width:454px;height:55px">Phone Number</div>
  <div class="field" style="left:614px;top:3827px;width:454px;height:55px">Reference</div>
  <div class="field area" style="left:130px;top:3904px;width:945px;height:95px">Message</div>
  <a class="btn" style="left:482px;top:4025px;width:241px;height:46px">Book Appointment</a>
</form>

<!-- Footer -->
<footer class="abs site-footer"></footer>
<div class="abs brand footer-logo">KAVRIN</div>
<span class="abs foot-social" style="left:101px"></span>
<span class="abs foot-social" style="left:131px"></span>
<span class="abs foot-social" style="left:161px"></span>
<div class="foot-col" style="left:367px">
  <h4>Contact Us</h4>
  <ul>
    <li><svg width="14" height="18" viewBox="0 0 24 30"><path d="M12 2a9 9 0 0 0-9 9c0 7 9 17 9 17s9-10 9-17a9 9 0 0 0-9-9z" fill="#fff"/><circle cx="12" cy="11" r="3.5" fill="var(--night)"/></svg>Lindenweg 12,</li>
    <li style="padding-left:24px">8003 Zurich, Switzerland</li>
    <li style="margin-top:12px"><svg width="14" height="14" viewBox="0 0 24 24"><path d="M6.6 10.8a15 15 0 0 0 6.6 6.6l2.2-2.2c.3-.3.7-.4 1-.2 1.1.4 2.3.6 3.6.6.6 0 1 .4 1 1V20c0 .6-.4 1-1 1A17 17 0 0 1 3 4c0-.6.4-1 1-1h3.5c.6 0 1 .4 1 1 0 1.3.2 2.5.6 3.6.1.3 0 .7-.2 1z" fill="#fff"/></svg>+41 44 318 27 60</li>
    <li style="margin-top:8px"><svg width="15" height="12" viewBox="0 0 24 18"><rect x="1" y="1" width="22" height="16" rx="2" fill="#fff"/><path d="M2 3l10 7 10-7" fill="none" stroke="var(--night)" stroke-width="2"/></svg>info@kavrin.ch</li>
  </ul>
</div>
<div class="foot-col" style="left:624px">
  <h4>QUICK LINKS</h4>
  <ul><li>Home</li><li>eCommerce</li><li>Online Marketing</li><li>Integration</li><li>Company</li></ul>
</div>
<div class="foot-col" style="left:884px">
  <h4>Other links</h4>
  <ul><li>Investment Resources</li><li>Customer Stories</li><li>FAQ</li><li>Privacy Policy</li><li>Terms Of Use</li></ul>
</div>
<div class="abs foot-line"></div>
<p class="abs copyright">Copyrights@2023.Kavrin.All Rights Reserved</p>

</body>
</html>
```